Local Flower Farm Needs Business Card Design

I need business cards designed for a flower farm based in Eudora, Kansas.
Business Info:
We are a local cut flower farm located in Eudora, Kansas, founded by Corinne Haldwick. What started as a passion for agriculture and search for more joy in daily life has blossomed into a small business dedicated to providing the community with beautiful, fresh, and sustainable flowers. We specialize in local, seasonal blooms, ensuring that every petal reflects the care and dedication we pour into our craft. Our mission is to deliver the highest quality flowers directly to our customers through local farmers markets and to florists who share our commitment to sustainability. Join us in celebrating the beauty of nature, one bloom at a time!
Contact Details:
Corinne Haldwick
Owner
Phone 913-555-0147
Facebook: Rosalind Thorpe Gardens
Instagram: @RosalindThorpeGardens
Website: RosalindThorpeGardens.example
Target Market(s)
Wholesale to Florists and Direct to Consumer via Farmers Market
Industry/Entity Type
Florist, Farm
Contact Information for Business Card
Name, Contact Info, Logo
Look and feel
Each slider illustrates characteristics of the customer's brand and the style your logo design should communicate.

```html
<!DOCTYPE html>
<html lang="en">
<head>
<meta charset="utf-8">
<title>Rosalind Thorpe Gardens — Business Card</title>
<link rel="stylesheet" href="https://fonts.googleapis.com/css2?family=Tinos:wght@400;700&display=swap">
<style>
  :root {
    --backdrop: #1d1e20;
    --card: #ffffff;
    --ink: #0e2426;
    --ink-soft: #4a4f50;
    --serif: "Tinos", "Times New Roman", serif;
  }
  * { box-sizing: border-box; margin: 0; padding: 0; }
  html, body {
    width: 1200px; height: 840px; overflow: hidden;
    background: var(--backdrop);
    font-family: var(--serif);
    color: var(--ink);
  }
  .canvas { position: relative; width: 1200px; height: 840px; }

  .card {
    position: absolute;
    width: 560px; height: 320px;
    background: var(--card);
    border-radius: 22px;
    overflow: hidden;
    box-shadow: 0 18px 40px rgba(0,0,0,.45);
  }
  .card--front { left: 70px; top: 70px; }
  .card--back  { left: 570px; top: 450px; }

  /* brand seal: invented name in a plain circle */
  .seal {
    position: absolute;
    display: flex; align-items: center; justify-content: center;
    border: 1.5px solid var(--ink);
    border-radius: 50%;
    text-align: center;
    text-transform: uppercase;
    font-weight: 400;
    color: var(--ink);
  }
  .card--front .seal {
    width: 220px; height: 220px;
    left: 170px; top: 50px;
    font-size: 22px; letter-spacing: 3px; line-height: 1.35;
  }
  .card--back .seal {
    width: 104px; height: 104px;
    right: 26px; top: 20px;
    font-size: 10.5px; letter-spacing: 1.4px; line-height: 1.35;
  }

  /* large brand name set as the back-side feature */
  .brand-feature {
    position: absolute;
    left: 22px; top: 0; bottom: 0; width: 250px;
    display: flex; flex-direction: column; justify-content: center;
    font-size: 40px; font-weight: 700;
    line-height: 1.08;
    text-transform: uppercase;
    letter-spacing: 1px;
    color: var(--ink);
  }

  .details {
    position: absolute;
    left: 290px; top: 136px; right: 16px;
  }
  .details__name {
    font-size: 21px; font-weight: 700;
    text-transform: uppercase; letter-spacing: .4px;
    line-height: 1.15;
    white-space: nowrap;
  }
  .details__role {
    font-size: 15px; color: var(--ink-soft);
    margin-bottom: 14px;
  }
  .contact-list { list-style: none; }
  .contact-list li {
    display: flex; align-items: center; gap: 7px;
    font-size: 14.5px; color: var(--ink-soft);
    line-height: 1.5;
    white-space: nowrap;
  }
  .contact-list svg { width: 13px; height: 13px; flex: none; }
</style>
</head>
<body>
<main class="canvas">

  <section class="card card--front" aria-label="Business card front">
    <div class="seal">Rosalind Thorpe<br>Gardens</div>
  </section>

  <section class="card card--back" aria-label="Business card back">
    <p class="brand-feature">Rosalind<br>Thorpe<br>Gardens</p>

    <div class="seal">Rosalind<br>Thorpe<br>Gardens</div>

    <div class="details">
      <h1 class="details__name">Corinne Haldwick</h1>
      <p class="details__role">Owner</p>
      <ul class="contact-list">
        <li>
          <svg viewBox="0 0 16 16" aria-hidden="true"><path fill="#0e2426" d="M3.5 1.5l2.2 2.6-1.2 1.6c.9 2 2.3 3.4 4.3 4.3l1.6-1.2 2.6 2.2-1.3 2.3C6.6 13.2 2.8 9.4 2.3 4.3z"/></svg>
          913-555-0147
        </li>
        <li>
          <svg viewBox="0 0 16 16" aria-hidden="true"><rect x="1.5" y="1.5" width="13" height="13" rx="3" fill="#0e2426"/></svg>
          Rosalind Thorpe Gardens
        </li>
        <li>
          <svg viewBox="0 0 16 16" aria-hidden="true"><rect x="1.5" y="1.5" width="13" height="13" rx="3" fill="#0e2426"/></svg>
          @RosalindThorpeGardens
        </li>
        <li>
          <svg viewBox="0 0 16 16" aria-hidden="true"><circle cx="8" cy="8" r="7" fill="#0e2426"/><ellipse cx="8" cy="8" rx="3" ry="7" fill="none" stroke="#fff" stroke-width="1"/><line x1="1" y1="8" x2="15" y2="8" stroke="#fff" stroke-width="1"/></svg>
          RosalindThorpeGardens.example
        </li>
      </ul>
    </div>
  </section>

</main>
</body>
</html>
```